Personal Chef Needs a Good Web Design

Hi everyone!
My name is Leo, I work as a private chef for last 10 years, traveling all around the world and cooking in private megayacht and villas.
I'm about to settle down in my hometown in Europe for a while. And therefore I need a website that will show my story, pics and recipes, nutritional advices and of course offer a Personal and Private Chef services( working for 4-5 families and bringing delicious food to their house).
My clients are extremely rich folks, but usually are down to earth ones.
I believe, the web site should be focused on attention to:
-VIP person's wife( as she is usually responsible for food for family) and be simple.
-to famous people agents and be on high level.

There will be about 10 different menus and 6 different service offers

--UPDATE--
Logo Design:
+My thoughts are- printed structure of the vegetable or fruit on a white font. Like you slice the buffalo tomato, put it in red paint and print it on the edge of the page. See attached files named logo. Can be any nice structured thing, like tomato, lemon, red cabbage etc.
+Classic logos with chef's hat or knives are good too.
+Need to have the space for me to add the name( the fonts can be provided)

Target Market(s)

Private person. 80% Russian clients.

Industry/Entity Type

Cooking

Coding

Coded - Design and coding required

Number of Pages Required

3 page

Requirements
Must have
• Contact form/ Request back call/ Schedule a free consultation
Nice to have
• The client will need to choose straight ahead from the range of services I offer, like:
• -Private Chef( cooking only for the client)
• -Personal Chef( cooking for around 5 clients, bringing the ready to be heated food to their door)
• -Romantic dinner for two
• -Professional Sommelier service
• -Build your kitchen( offering design, equipment and that will fit your requirements)
• -Other( flowers, waiters, barista, equipment rental)
• So this column should go right after the introduction/aboutme part and will lead to separate pages with how-it-works thing for each.

```html
<!DOCTYPE html>
<html lang="en">
<head>
<meta charset="utf-8">
<title>Leo's Table</title>
<link rel="stylesheet" href="https://fonts.googleapis.com/css2?family=Nunito+Sans:wght@400;600;700&family=Open+Sans:wght@400;600;700&display=swap">
<style>
:root{
  --accent:#d9944a;
  --ink:#1e1e1e;
  --text:#555;
  --muted:#777;
  --line:#d6d6d6;
  --bg:#fff;
}
*{box-sizing:border-box;margin:0;padding:0}
html,body{width:1200px;height:2446px;overflow:hidden;background:var(--bg)}
body{position:relative;font-family:"Open Sans",sans-serif;color:var(--text)}
.site-header{position:absolute;left:0;top:0;width:1200px;height:81px;border-bottom:2px solid #e6e6e6}
.brand{position:absolute;left:98px;top:26px;font-family:"Nunito Sans",sans-serif;font-weight:600;font-size:24px;color:var(--ink)}
.menu-btn{position:absolute;left:1066px;top:24px;width:35px;height:35px;border:2px solid var(--accent);border-radius:50%}
.menu-btn span{position:absolute;left:10px;width:12px;height:2px;background:var(--accent)}
.section-title{position:absolute;left:0;width:1200px;text-align:center;font-family:"Nunito Sans",sans-serif;font-weight:700;font-size:32px;color:var(--ink);letter-spacing:.5px}
.recipe-card{position:absolute;width:491px;height:196px;border:1px solid var(--line);box-shadow:0 1px 3px rgba(0,0,0,.18);background:#fff;display:flex}
.recipe-card.featured{background:var(--accent)}
.recipe-photo{width:188px;height:100%;flex:none}
.recipe-body{padding:16px 0 0 20px}
.recipe-name{font-family:"Nunito Sans",sans-serif;font-weight:700;font-size:20px;color:var(--ink);margin-bottom:9px}
.recipe-list{list-style:none}
.recipe-list li{position:relative;padding-left:19px;font-size:10.8px;line-height:26px;color:var(--text);white-space:nowrap}
.recipe-list li::before{content:"";position:absolute;left:2px;top:8px;width:5px;height:9px;border:solid var(--accent);border-width:0 2.5px 2.5px 0;transform:rotate(40deg)}
.view-more{display:block;margin-top:6px;font-size:11px;font-weight:700;color:var(--accent);text-decoration:none}
.featured .recipe-name,.featured .recipe-list li,.featured .view-more{color:#fff}
.featured .recipe-list li::before{border-color:#fff}
.chef-frame{position:absolute;left:98px;top:1397px;width:345px;height:408px;border:1px solid #999;padding:5px}
.chef-photo{width:100%;height:100%;background:linear-gradient(135deg,#5c4a3a,#a89a8c 45%,#e8e6e2 70%,#7a6a58)}
.about{position:absolute;left:502px;top:1397px;width:600px}
.about h2{font-family:"Nunito Sans",sans-serif;font-weight:700;font-size:32px;color:var(--ink);margin-bottom:18px}
.about p{font-size:10.9px;line-height:32px;color:var(--text);margin-bottom:32px}
.btn{display:inline-block;background:var(--accent);color:#fff;font-weight:700;font-size:11px;border:none;text-decoration:none;text-align:center}
.read-more{position:absolute;left:502px;top:1767px;width:120px;height:33px;line-height:33px}
.divider{position:absolute;left:0;top:1883px;width:1200px;height:5px;background:var(--accent)}
.sub-title{position:absolute;font-family:"Nunito Sans",sans-serif;font-weight:600;font-size:15px;color:var(--ink)}
.field-label{position:absolute;font-size:11px;color:var(--text)}
.field{position:absolute;border:1px solid #aaa;background:#fff}
.submit{position:absolute;left:642px;top:2297px;width:88px;height:35px;line-height:35px;font-size:13px}
.info-row{position:absolute;left:810px;display:flex;align-items:center}
.info-icon{width:34px;height:34px;border:1px solid #999;border-radius:50%;display:flex;align-items:center;justify-content:center;margin-right:46px}
.info-text{font-size:12px;line-height:24px;color:var(--text)}
.hours{position:absolute;left:810px;top:2254px;font-size:12px;color:var(--text);border-collapse:collapse}
.hours td{height:26px;padding:0}
.hours td:first-child{width:140px}
.site-footer{position:absolute;left:98px;top:2371px;width:1004px;border-top:1px solid var(--line)}
.copyright{position:absolute;left:0;top:28px;font-size:11.5px;color:var(--text);white-space:nowrap}
.social{position:absolute;left:856px;top:24px;display:flex;gap:16px}
.social span{width:25px;height:25px;background:#9a9a9a;border-radius:4px}
</style>
</head>
<body>
<header class="site-header">
  <div class="brand">Leo's Table</div>
  <div class="menu-btn" aria-label="Menu"><span style="top:11px"></span><span style="top:16px"></span><span style="top:21px"></span></div>
</header>

<h1 class="section-title" style="top:136px">MY RECIPES</h1>

<article class="recipe-card featured" style="left:98px;top:212px">
  <div class="recipe-photo" role="img" aria-label="Fish tacos with slaw and lime" style="background:linear-gradient(135deg,#c9b49a,#c88a4a 50%,#8a6aa0)"></div>
  <div class="recipe-body"><h3 class="recipe-name">SEAFOOD</h3><ul class="recipe-list"><li>Thai Style Mahi with a Coconut Coucous</li><li>Garlic and Herb Crusted Seabass</li><li>Poached Halibut with Leeks &amp; Grape Tomatoes</li><li>Miso Salmon with a Ginger Jasmine Rice</li></ul><a class="view-more" href="#">VIEW MORE &gt;&gt;</a></div>
</article>
<article class="recipe-card" style="left:610px;top:212px">
  <div class="recipe-photo" role="img" aria-label="Sliced roast beef tenderloin with herbs" style="background:linear-gradient(135deg,#3a2a22,#8a3a36 50%,#5a4030)"></div>
  <div class="recipe-body"><h3 class="recipe-name">BEEF</h3><ul class="recipe-list"><li>Grilled Teriyaki Steak Tips</li><li>Slow Cooked Smokey Chipotle Tacos</li><li>Beef Tenderloin in a Mushroom Brandy Sauce</li><li>Penne Bolognese or Classic Meat Lasagna</li></ul><a class="view-more" href="#">VIEW MORE &gt;&gt;</a></div>
</article>

<article class="recipe-card" style="left:98px;top:430px">
  <div class="recipe-photo" role="img" aria-label="Roasted chicken pieces" style="background:linear-gradient(135deg,#3a2418,#9a5a2a 50%,#5a3018)"></div>
  <div class="recipe-body"><h3 class="recipe-name">CHICKEN</h3><ul class="recipe-list"><li>Chicken with Arugula with a Basil Pasta Salad</li><li>Baked Chicken with Sweet Potato and Radish</li><li>Marsala, Mushrooms, Pancetta, Marsala wine</li><li>Curry Spiced Chicken Breast with a Yogurt</li></ul><a class="view-more" href="#">VIEW MORE &gt;&gt;</a></div>
</article>
<article class="recipe-card" style="left:610px;top:430px">
  <div class="recipe-photo" role="img" aria-label="Roast pork with vegetables" style="background:linear-gradient(135deg,#3a3028,#b07040 50%,#6a3a2a)"></div>
  <div class="recipe-body"><h3 class="recipe-name">PORK</h3><ul class="recipe-list"><li>Oriental Sweet and Sour Pork</li><li>Maple Dijon Glazed Pork Medallions</li><li>Crispy Corn Flake Pan Fried Pork Chops</li><li>Creamy Pork Chops with Mushrooms, Hericot</li></ul><a class="view-more" href="#">VIEW MORE &gt;&gt;</a></div>
</article>

<article class="recipe-card" style="left:98px;top:649px">
  <div class="recipe-photo" role="img" aria-label="Fried breaded shrimp on a plate" style="background:linear-gradient(135deg,#f0e6dc,#d8783a 50%,#c05a28)"></div>
  <div class="recipe-body"><h3 class="recipe-name">SEAFOOD</h3><ul class="recipe-list"><li>Chicken with Arugula with a Basil Pasta Salad</li><li>Baked Chicken with Sweet Potato and Radish</li><li>Marsala, Mushrooms, Pancetta, Marsala wine</li><li>Curry Spiced Chicken Breast with a Yogurt</li></ul><a class="view-more" href="#">VIEW MORE &gt;&gt;</a></div>
</article>
<article class="recipe-card" style="left:610px;top:649px">
  <div class="recipe-photo" role="img" aria-label="Beef stir fry with green onions in a bowl" style="background:linear-gradient(135deg,#e8e8e8,#3a2a2a 45%,#4a6a2a)"></div>
  <div class="recipe-body"><h3 class="recipe-name">BEEF</h3><ul class="recipe-list"><li>Oriental Sweet and Sour Pork</li><li>Maple Dijon Glazed Pork Medallions</li><li>Crispy Corn Flake Pan Fried Pork Chops</li><li>Creamy Pork Chops with Mushrooms, Hericot</li></ul><a class="view-more" href="#">VIEW MORE &gt;&gt;</a></div>
</article>

<article class="recipe-card" style="left:98px;top:867px">
  <div class="recipe-photo" role="img" aria-label="Chicken with mushroom sauce" style="background:linear-gradient(135deg,#d8cfc0,#8a7040 50%,#e8e0d0)"></div>
  <div class="recipe-body"><h3 class="recipe-name">CHICKEN</h3><ul class="recipe-list"><li>Chicken with Arugula with a Basil Pasta Salad</li><li>Baked Chicken with Sweet Potato and Radish</li><li>Marsala, Mushrooms, Pancetta, Marsala wine</li><li>Curry Spiced Chicken Breast with a Yogurt</li></ul><a class="view-more" href="#">VIEW MORE &gt;&gt;</a></div>
</article>
<article class="recipe-card" style="left:610px;top:867px">
  <div class="recipe-photo" role="img" aria-label="Pork chop in creamy sauce" style="background:linear-gradient(135deg,#d87a2a,#6a4028 50%,#d8c8a8)"></div>
  <div class="recipe-body"><h3 class="recipe-name">PORK</h3><ul class="recipe-list"><li>Oriental Sweet and Sour Pork</li><li>Maple Dijon Glazed Pork Medallions</li><li>Crispy Corn Flake Pan Fried Pork Chops</li><li>Creamy Pork Chops with Mushrooms, Hericot</li></ul><a class="view-more" href="#">VIEW MORE &gt;&gt;</a></div>
</article>

<article class="recipe-card" style="left:98px;top:1086px">
  <div class="recipe-photo" role="img" aria-label="Baked salmon with lemon and tomatoes" style="background:linear-gradient(135deg,#e8b030,#a05030 45%,#c05040)"></div>
  <div class="recipe-body"><h3 class="recipe-name">SEAFOOD</h3><ul class="recipe-list"><li>Chicken with Arugula with a Basil Pasta Salad</li><li>Baked Chicken with Sweet Potato and Radish</li><li>Marsala, Mushrooms, Pancetta, Marsala wine</li><li>Curry Spiced Chicken Breast with a Yogurt</li></ul><a class="view-more" href="#">VIEW MORE &gt;&gt;</a></div>
</article>
<article class="recipe-card" style="left:610px;top:1086px">
  <div class="recipe-photo" role="img" aria-label="Grilled steak with tomatoes and potatoes" style="background:linear-gradient(135deg,#f0e8e0,#6a3a28 50%,#3a2218)"></div>
  <div class="recipe-body"><h3 class="recipe-name">BEEF</h3><ul class="recipe-list"><li>Oriental Sweet and Sour Pork</li><li>Maple Dijon Glazed Pork Medallions</li><li>Crispy Corn Flake Pan Fried Pork Chops</li><li>Creamy Pork Chops with Mushrooms, Hericot</li></ul><a class="view-more" href="#">VIEW MORE &gt;&gt;</a></div>
</article>

<div class="chef-frame"><div class="chef-photo" role="img" aria-label="Chef in white jacket with arms crossed in a bakery kitchen"></div></div>
<section class="about">
  <h2>LEO'S TABLE</h2>
  <p>At vero eos et accusamus et iusto odio dignissimos ducimus qui blanditiis praesentium voluptatum deleniti at que corrupti quos dolores et quas molestias excepturi.</p>
  <p>Sint occaecati cupiditate non provident, similique sunt in culpa qui officia deserunt mollitia animi, id est lab orum et dolorum fuga. Et harum quidem rerum facilis est et expedita distinctio. Nam libero tempore, cum soluta nobis est eligendi optio cumque nihil impedit quo minus id quod maxime placeat facere possimum nis voluptas assumenda est, omnis dolor repellendus. Temporibus autem quibusdam et aut officiis debitis aut rerum necessitatibus saepe eveniet ut et voluptates. Et harum quidem rerum facilis est et expedita dist inctio. Nam libero tempore, cum&nbsp; eligendi optio cumque nihil impe.</p>
</section>
<a class="btn read-more" href="#">READ MORE &gt;&gt;</a>

<div class="divider"></div>
<h2 class="section-title" style="top:1925px">CONTACT US</h2>

<div class="sub-title" style="left:98px;top:2005px">CONTACT FORM</div>
<div class="field-label" style="left:98px;top:2047px">NAME :</div>
<div class="field-label" style="left:419px;top:2047px">PHONE NO :</div>
<div class="field" style="left:99px;top:2075px;width:311px;height:33px"></div>
<div class="field" style="left:419px;top:2075px;width:311px;height:33px"></div>
<div class="field-label" style="left:98px;top:2117px">EMAIL :</div>
<div class="field" style="left:99px;top:2141px;width:631px;height:33px"></div>
<div class="field-label" style="left:98px;top:2183px">MESSAGE :</div>
<div class="field" style="left:99px;top:2207px;width:631px;height:82px"></div>
<button class="btn submit">SUBMIT</button>

<div class="sub-title" style="left:810px;top:2005px">CONTACT INFORMATION</div>
<div class="info-row" style="top:2050px">
  <span class="info-icon"><svg width="14" height="16" viewBox="0 0 14 16"><path d="M7 1a5 5 0 0 0-5 5c0 4 5 9 5 9s5-5 5-9a5 5 0 0 0-5-5z" fill="var(--accent)"/><circle cx="7" cy="6" r="1.8" fill="#fff"/></svg></span>
  <span class="info-text">Street # 200 - 318<br>Alder Falls 40512</span>
</div>
<div class="info-row" style="top:2106px">
  <span class="info-icon"><svg width="16" height="12" viewBox="0 0 16 12"><rect x="1" y="1" width="14" height="10" rx="1" fill="var(--accent)"/><path d="M1 2l7 5 7-5" stroke="#fff" stroke-width="1.4" fill="none"/></svg></span>
  <span class="info-text">info@leostable.com</span>
</div>
<div class="info-row" style="top:2162px">
  <span class="info-icon"><svg width="14" height="14" viewBox="0 0 14 14"><path d="M3 1l2.5 3-1.5 1.5a8 8 0 0 0 4.5 4.5L10 8.5l3 2.5-1.5 2C6 13 1 8 1 2.5z" fill="var(--accent)"/></svg></span>
  <span class="info-text">1 - 555 - 014 - 2273</span>
</div>
<div class="sub-title" style="left:810px;top:2228px">OPENING HOURS</div>
<table class="hours">
  <tr><td>Monday - Wednesday :</td><td>10:00 am - 10:00 pm</td></tr>
  <tr><td>Thursday &amp; Friday :</td><td>10:00 am - 10:00 pm</td></tr>
  <tr><td>Saturday &amp; Sunday</td><td>9:00 am - 11:00 pm</td></tr>
</table>

<footer class="site-footer">
  <div class="copyright">Copyrights © 2016, Leo's Table . All Rights Reserved.</div>
  <div class="social" aria-label="Social links"><span></span><span></span><span></span><span></span></div>
</footer>
</body>
</html>
```